SkyvornQ Business Cards and Stationary Design

Need a design for our business cards and stationary. I want to carry on the theme of the logo. I want the business cards to have a design on the back. I would like the business cards and the stationary to carry the same theme, design scheme, and branding

Target Market(s)

Airlines and Maintenance Facilities

Industry/Entity Type

Aviation

Contact Information for Business Card

Name
Position Title
Address: 4827 Trellis Hollow Road, Marren Key, Florida, 34951
Office Number
Mobile Number
Email
Website

Font styles to use
Serif
Sans Serif

Colors

Designer to choose colors to be used in the design.

```html
<!DOCTYPE html>
<html lang="en">
<head>
<meta charset="utf-8">
<title>SkyvornQ Business Card</title>
<link href="https://fonts.googleapis.com/css2?family=Open+Sans:wght@400;600;700&display=swap" rel="stylesheet">
<style>
  :root {
    --backdrop: #d9d9d9;
    --card: #fbfbfb;
    --navy: #14295a;
    --sky: #1e95dc;
    --ink: #2a3550;
    --muted: #4a5570;
  }
  * { box-sizing: border-box; margin: 0; padding: 0; }
  html, body { width: 1200px; height: 852px; overflow: hidden; }
  body {
    background: var(--backdrop);
    font-family: "Open Sans", Arial, sans-serif;
    position: relative;
  }
  .card {
    position: absolute;
    top: 277px;
    width: 520px;
    height: 298px;
    background: var(--card);
    border-radius: 18px;
    box-shadow: 0 6px 18px rgba(0,0,0,0.18);
    overflow: hidden;
  }
  .card--front { left: 50px; }
  .card--back { left: 630px; }

  .brand {
    display: flex;
    align-items: center;
    gap: 12px;
    color: var(--navy);
    font-weight: 700;
    letter-spacing: 4px;
    text-transform: uppercase;
    white-space: nowrap;
  }
  .brand__dot {
    border-radius: 50%;
    background: var(--sky);
    flex: none;
  }

  /* front */
  .card--front .brand {
    position: absolute;
    left: 0; right: 0; top: 98px;
    justify-content: center;
    font-size: 36px;
  }
  .card--front .brand__dot { width: 30px; height: 30px; }
  .web-rule {
    position: absolute;
    left: 0; right: 0; top: 180px;
    display: flex;
    align-items: center;
    justify-content: center;
    gap: 14px;
    font-size: 13px;
    color: var(--muted);
    letter-spacing: 1px;
  }
  .web-rule__line { width: 80px; height: 2px; background: var(--sky); }
  .edge-band {
    position: absolute;
    left: 0; right: 0; bottom: 0;
    height: 10px;
    display: flex;
  }
  .edge-band__navy { flex: 1; background: var(--navy); }
  .edge-band__sky { flex: 1; background: var(--sky); }

  /* back */
  .card--back .brand {
    position: absolute;
    left: 40px; top: 128px;
    font-size: 26px;
    letter-spacing: 3px;
  }
  .card--back .brand__dot { width: 22px; height: 22px; }
  .contact {
    position: absolute;
    left: 300px; top: 62px;
    color: var(--ink);
    white-space: nowrap;
  }
  .contact__name { font-size: 20px; font-weight: 600; color: var(--sky); line-height: 1.1; }
  .contact__role { font-size: 11.5px; color: var(--muted); margin: 2px 0 14px 10px; }
  .contact__list { list-style: none; margin-left: 10px; }
  .contact__item {
    display: flex;
    align-items: center;
    gap: 8px;
    font-size: 11.5px;
    line-height: 17px;
  }
  .contact__item svg { width: 11px; height: 11px; fill: var(--navy); flex: none; }
  .contact__address {
    font-size: 11.5px;
    line-height: 15px;
    margin: 6px 0 0 29px;
  }
</style>
</head>
<body>
  <section class="card card--front">
    <div class="brand"><span class="brand__dot"></span>SkyvornQ</div>
    <div class="web-rule">
      <span class="web-rule__line"></span>
      <span class="web-rule__url">www.skyvornq.com</span>
      <span class="web-rule__line"></span>
    </div>
    <div class="edge-band"><span class="edge-band__navy"></span><span class="edge-band__sky"></span></div>
  </section>

  <section class="card card--back">
    <div class="brand"><span class="brand__dot"></span>SkyvornQ</div>
    <div class="contact">
      <p class="contact__name">Marla Quenby</p>
      <p class="contact__role">Managing Director</p>
      <ul class="contact__list">
        <li class="contact__item">
          <svg viewBox="0 0 12 12" aria-hidden="true"><path d="M1 3c0-1 1-2 2-2h6c1 0 2 1 2 2v1H8V3H4v1H1zM2 5h8l1 6H1z"/></svg>
          555 0142 318
        </li>
        <li class="contact__item">
          <svg viewBox="0 0 12 12" aria-hidden="true"><path d="M3 0h6a1 1 0 0 1 1 1v10a1 1 0 0 1-1 1H3a1 1 0 0 1-1-1V1a1 1 0 0 1 1-1zm0 2v7h6V2z"/></svg>
          555 0187 264
        </li>
        <li class="contact__item">
          <svg viewBox="0 0 12 12" aria-hidden="true"><path d="M0 2h12v8H0zm1 1v.4l5 3.2 5-3.2V3z"/></svg>
          marla@skyvornq.com
        </li>
        <li class="contact__item">
          <svg viewBox="0 0 12 12" aria-hidden="true"><circle cx="6" cy="6" r="5.5"/><path d="M0.5 6h11M6 0.5c-2 2-2 9 0 11M6 0.5c2 2 2 9 0 11" stroke="#fbfbfb" stroke-width="0.8" fill="none"/></svg>
          www.skyvornq.com
        </li>
      </ul>
      <p class="contact__address">4827 Trellis Hollow Road,<br>Marren Key, Florida, 34951</p>
    </div>
  </section>
</body>
</html>
```